Professional Photography Business cards

I need business cards that include my logo which I have uploaded. I run a photography business. I am open to ideas but I would like one side to have my logo and the other side to have my contact info. I don't have a website made but I do own a website domain. I have uploaded 2 different logo color schemes. My business colors are Blue, black , and white.

Business Name
Business Phone Number
Business Email
Business Website address
Instagram

Industry/Entity Type

Professional Photography

Contact Information for Business Card

Phone Number: 916-384-7702 email: info@tlane-studio.example Instagram: @t.lanestudio website doman- www.tlane-studio.example

Requirements
Must have
• I like the idea of a business card with a full black background front and back of card. My colors must include royal blue, black, and white

```html
<!DOCTYPE html>
<html lang="en">
<head>
<meta charset="utf-8">
<title>T. Lane Studio — Business Cards</title>
<link rel="stylesheet" href="https://fonts.googleapis.com/css2?family=Arimo:wght@400;700&display=swap">
<style>
  :root {
    --backdrop: #3b3b3c;
    --card: #1c1c1d;
    --royal-blue: #2e3a9c;
    --white: #ffffff;
    --emboss: #2a2a2b;
    --emboss-edge: #5c5c5e;
  }
  * { box-sizing: border-box; margin: 0; padding: 0; }
  html, body {
    width: 1200px;
    height: 1059px;
    overflow: hidden;
    background: var(--backdrop);
    font-family: "Arimo", Arial, sans-serif;
  }
  .canvas {
    position: relative;
    width: 1200px;
    height: 1059px;
  }
  .card {
    position: absolute;
    background: var(--card);
    border-radius: 24px;
    box-shadow: 0 14px 28px rgba(0, 0, 0, 0.55);
    overflow: hidden;
  }
  .card--front { left: 256px; top: 100px; width: 688px; height: 391px; }
  .card--back  { left: 253px; top: 537px; width: 694px; height: 394px; }

  .brand {
    position: absolute;
    display: flex;
    align-items: center;
    gap: 14px;
    white-space: nowrap;
  }
  .brand__dot {
    width: 18px;
    height: 18px;
    border-radius: 50%;
  }
  .brand__name {
    font-weight: 700;
    font-size: 46px;
    letter-spacing: 1px;
  }
  .card--front .brand {
    left: 50%; top: 188px;
    transform: translate(-50%, -50%);
  }
  .card--front .brand__dot { background: var(--emboss-edge); }
  .card--front .brand__name { color: var(--emboss-edge); }

  .card--back .brand {
    left: 50%; top: 133px;
    transform: translate(-50%, -50%);
  }
  .card--back .brand__dot { background: var(--royal-blue); }
  .card--back .brand__name { color: var(--white); }

  .holder {
    position: absolute;
    right: 368px;
    top: 266px;
    text-align: right;
  }
  .holder__name {
    color: var(--royal-blue);
    font-weight: 700;
    font-size: 26px;
    line-height: 30px;
  }
  .holder__role {
    color: var(--white);
    font-size: 16px;
    line-height: 20px;
  }
  .divider {
    position: absolute;
    left: 346px;
    top: 257px;
    width: 1px;
    height: 73px;
    background: var(--royal-blue);
  }
  .contacts {
    position: absolute;
    left: 367px;
    top: 251px;
    list-style: none;
  }
  .contacts__item {
    display: flex;
    align-items: center;
    height: 21px;
    color: var(--white);
    font-size: 16px;
  }
  .contacts__icon {
    width: 12px;
    height: 12px;
    margin-right: 9px;
    flex: none;
  }
  .contacts__bullet {
    width: 10px;
    height: 10px;
    margin: 0 10px 0 1px;
    border-radius: 50%;
    background: var(--royal-blue);
    flex: none;
  }
</style>
</head>
<body>
<main class="canvas">

  <section class="card card--front" aria-label="Card front">
    <div class="brand">
      <span class="brand__dot"></span>
      <span class="brand__name">T. Lane Studio</span>
    </div>
  </section>

  <section class="card card--back" aria-label="Card back">
    <div class="brand">
      <span class="brand__dot"></span>
      <span class="brand__name">T. Lane Studio</span>
    </div>

    <div class="holder">
      <p class="holder__name">Dana Whitfield</p>
      <p class="holder__role">Managing Director</p>
    </div>

    <span class="divider"></span>

    <ul class="contacts">
      <li class="contacts__item">
        <svg class="contacts__icon" viewBox="0 0 24 24" aria-hidden="true">
          <path fill="#2e3a9c" d="M6.6 10.8a15.1 15.1 0 0 0 6.6 6.6l2.2-2.2a1 1 0 0 1 1-.25 11.4 11.4 0 0 0 3.6.6 1 1 0 0 1 1 1V20a1 1 0 0 1-1 1A17 17 0 0 1 3 4a1 1 0 0 1 1-1h3.5a1 1 0 0 1 1 1c0 1.25.2 2.45.6 3.6a1 1 0 0 1-.25 1z"/>
        </svg>
        916-384-7702
      </li>
      <li class="contacts__item">
        <svg class="contacts__icon" viewBox="0 0 24 24" aria-hidden="true">
          <rect x="2" y="5" width="20" height="14" fill="#2e3a9c"/>
          <path d="M2 5l10 8 10-8M2 19l7-7M22 19l-7-7" fill="none" stroke="#1c1c1d" stroke-width="1.6"/>
        </svg>
        info@tlane-studio.example
      </li>
      <li class="contacts__item">
        <svg class="contacts__icon" viewBox="0 0 24 24" aria-hidden="true">
          <circle cx="12" cy="12" r="10" fill="#2e3a9c"/>
          <path d="M2 12h20M12 2c3 3 3 17 0 20M12 2c-3 3-3 17 0 20" fill="none" stroke="#1c1c1d" stroke-width="1.4"/>
        </svg>
        www.tlane-studio.example
      </li>
      <li class="contacts__item">
        <span class="contacts__bullet"></span>
        @t.lanestudio
      </li>
    </ul>
  </section>

</main>
</body>
</html>
```